Coastal Learner Bureau business cards

Australian company about to start offering its services. We recruit international students to come to study English, vocational education and postgraduate courses in Australia. We help them find the institution and select the right city they want to come to Australia. We are a young, online oriented and supportive agency. Our clients are between 18 and 35 years old, mainly University students, young professionals or people with work experience. We provide much more information that any other agency offer. We administrate a Facebook group with more than 11.000 members that daily ask questions about general information when coming to Australia, while they are here and even after they leave the country

Target Market(s)

International students from South America, Central America and Europe

Industry/Entity Type

Student

Contact Information for Business Card

Tomas Bilbrea
Managing Director
tomas@kelvarin.com.au
www.kelvoria.com.au
+61 491058264
Melbourne, Australia

Font styles to use
Serif
Sans Serif

Colors

Designer to choose colors to be used in the design.

Requirements
Must have
• Horizontal design
• Standard business card size and shape. If font uses green or yellow colours, they will have to match the ones from the logo
Nice to have
• UPDATE: Use the contents of the green image to design one of the card sides. Use our logo in the background of that side as watermark.
• Passport image, or immigration stamps. A picture of the Yarra River (from Melbourne) would be cool as well.
Should not have
• Non-standard business card size and shape
• Not black as the background colour of any sides as we are not a VIP agency or a hight class service. We are orientes to young people and they like colours, pictures, something attractive.
• Vertical design
• NO YELLOW or BLACK AS THE BACKGROUND COLOUR OF ANY SIDE OF THE BIZ CARD

```html
<!DOCTYPE html>
<html lang="en">
<head>
<meta charset="utf-8">
<title>Kelvoria business cards</title>
<link rel="stylesheet" href="https://fonts.googleapis.com/css2?family=Arimo:wght@400;700&display=swap">
<style>
  :root {
    --brand-green: #0b5b38;
    --brand-green-dark: #084a2d;
    --brand-yellow: #d8b21e;
    --card-white: #fbfbfb;
    --page-bg: #e9ebea;
    --text-light: #ffffff;
  }
  * { box-sizing: border-box; margin: 0; padding: 0; }
  html, body { width: 1200px; height: 997px; overflow: hidden; }
  body {
    background: var(--page-bg);
    font-family: "Arimo", Arial, sans-serif;
    position: relative;
  }
  .card {
    position: absolute;
    left: 240px;
    width: 720px;
    height: 411px;
    background: var(--card-white);
    overflow: hidden;
    box-shadow: 0 6px 20px rgba(0,0,0,.18);
  }
  .card--front { top: 60px; }
  .card--back { top: 526px; }

  /* front */
  .front__logo {
    position: absolute;
    left: 0; right: 0; top: 0; height: 290px;
    display: flex; align-items: center; justify-content: center; gap: 18px;
  }
  .brand-mark {
    width: 34px; height: 34px; border-radius: 50%;
    background: var(--brand-yellow);
    flex: none;
  }
  .brand-name {
    font-weight: 700;
    color: var(--brand-green);
    letter-spacing: 1px;
    white-space: nowrap;
  }
  .front__logo .brand-name { font-size: 88px; }
  .front__stripes {
    position: absolute; left: 0; right: 0; top: 290px; height: 22px;
    background: linear-gradient(
      to bottom,
      var(--brand-green) 0 4px,
      var(--brand-yellow) 4px 8px,
      var(--brand-green) 8px 13px,
      var(--brand-yellow) 13px 17px,
      var(--brand-green) 17px 22px);
  }
  .front__band {
    position: absolute; left: 0; right: 0; top: 312px; bottom: 0;
    background: var(--brand-green);
    display: flex; align-items: center; justify-content: center;
  }
  .tagline {
    color: #e6eee9;
    font-weight: 700;
    font-size: 21px;
    letter-spacing: 1px;
  }

  /* back */
  .back__contact {
    position: absolute; left: 0; top: 0; bottom: 0; width: 390px;
    background: linear-gradient(160deg, var(--brand-green) 0%, var(--brand-green-dark) 100%);
    color: var(--text-light);
    padding: 86px 0 0 40px;
  }
  .person__name { font-weight: 700; font-size: 20px; letter-spacing: .5px; }
  .person__role { color: var(--brand-yellow); font-size: 16px; margin-top: 3px; }
  .office { margin-top: 40px; font-size: 16px; line-height: 1.3; }
  .office__name { color: var(--brand-yellow); font-weight: 700; font-size: 19px; margin-bottom: 2px; }
  .channels { margin-top: 28px; list-style: none; font-size: 17px; }
  .channels li { display: flex; align-items: center; gap: 12px; height: 30px; white-space: nowrap; }
  .channel__icon {
    width: 22px; height: 22px; border-radius: 50%;
    background: var(--brand-yellow);
    display: flex; align-items: center; justify-content: center;
    flex: none;
  }
  .back__stripes {
    position: absolute; top: 0; bottom: 0; left: 390px; width: 34px;
    background: linear-gradient(
      to right,
      var(--brand-green) 0 5px,
      var(--brand-yellow) 5px 11px,
      var(--brand-green) 11px 18px,
      var(--brand-yellow) 18px 24px,
      var(--brand-green) 24px 34px);
  }
  .back__brand {
    position: absolute; left: 424px; right: 0; top: 0; bottom: 0;
  }
  .back__logo {
    position: absolute; left: 0; right: 0; top: 90px; height: 130px;
    display: flex; align-items: center; justify-content: center; gap: 12px;
  }
  .back__logo .brand-mark { width: 24px; height: 24px; }
  .back__logo .brand-name { font-size: 48px; }
  .website {
    position: absolute; right: 24px; bottom: 64px;
    color: var(--brand-green);
    font-weight: 700; font-size: 18px; letter-spacing: .6px;
    white-space: nowrap;
  }
</style>
</head>
<body>

<section class="card card--front" aria-label="Card front">
  <div class="front__logo">
    <span class="brand-mark"></span>
    <span class="brand-name">Kelvoria</span>
  </div>
  <div class="front__stripes"></div>
  <div class="front__band">
    <p class="tagline">Hacemos más por ti!</p>
  </div>
</section>

<section class="card card--back" aria-label="Card back">
  <div class="back__contact">
    <p class="person__name">TOMAS BILBREA</p>
    <p class="person__role">Managing Director</p>

    <div class="office">
      <p class="office__name">KELVORIA</p>
      <p>42 Harbour Lane, Suite 300</p>
      <p>Docklands, VIC 3008</p>
    </div>

    <ul class="channels">
      <li><span class="channel__icon"></span>kelvoria</li>
      <li>
        <span class="channel__icon">
          <svg width="14" height="14" viewBox="0 0 24 24" aria-hidden="true">
            <path fill="#0b5b38" d="M6.6 10.8a15 15 0 0 0 6.6 6.6l2.2-2.2c.3-.3.7-.4 1-.2 1.1.4 2.3.6 3.6.6.6 0 1 .4 1 1V20c0 .6-.4 1-1 1A17 17 0 0 1 3 4c0-.6.4-1 1-1h3.5c.6 0 1 .4 1 1 0 1.3.2 2.5.6 3.6.1.3 0 .7-.2 1z"/>
          </svg>
        </span>+61 491058264
      </li>
      <li>
        <span class="channel__icon">
          <svg width="13" height="13" viewBox="0 0 24 24" aria-hidden="true">
            <rect x="2" y="5" width="20" height="14" rx="2" fill="#0b5b38"/>
            <path d="M3 6l9 7 9-7" stroke="#d8b21e" stroke-width="2" fill="none"/>
          </svg>
        </span>tomas@kelvarin.com.au
      </li>
    </ul>
  </div>
  <div class="back__stripes"></div>
  <div class="back__brand">
    <div class="back__logo">
      <span class="brand-mark"></span>
      <span class="brand-name">Kelvoria</span>
    </div>
    <p class="website">WWW.KELVORIA.COM.AU</p>
  </div>
</section>

</body>
</html>
```